Website design for legal tech start up in Switzerland (B2B)

We are for a legal tech start up in Switzerland called KOVA. We have been running since August 2016. This will be our first live website.

We need a website designed and business card design for our start-up in Switzerland. We also need the Web design to be converted into HTML and CSS files.

Function of website:
• To inform potential customers of our services
• Form a key part of our digital marketing and sales footprint.
• Branding

Please find attached logo.
Updates

Project Deadline Extended Reason: Giving us time to review submissions and provide opportunity for more submissions. Added Thursday, February 16, 2017

Project Deadline Extended
Reason: Looking for more idea's not necessarily set on blue and grey colours only.

Target Market(s)

B2B tech powered legal services.

Industry/Entity Type

Legal

Contact Information for Business Card

Lean and slick design.

Coding

Coded - Design and coding required

Number of Pages Required

5+ page

Requirements
Must have
• VERY LEAN AND CLEAN DESIGN!
• We have received many great standard designs, but we are looking for something more out-of-the box: You can get inspiration from these designs: http://www.pixelvane.com/websites/clean/
• Thanks!!
• Easy content management system
• Well structured coding for additional development
• Responsive webpage for all types of devices
• SEO optimized
• Tabs (Home, services, team, careers, blog, contact us)
• Colour scheme complementary to logo
Nice to have
• Look and Design - Approachable, High-tech, Modern
• Easy to add chat bot capability in future
Should not have
• Too busy/ too much clutter
• Not take to long to load

```html
<!DOCTYPE html>
<html lang="en">
<head>
<meta charset="utf-8">
<title>KOVA – Legal Startup Company</title>
<link rel="stylesheet" href="https://fonts.googleapis.com/css2?family=Open+Sans:wght@700;800&family=Roboto:wght@300;400;500;700&display=swap">
<style>
:root{
  --navy:#22406f;
  --navy-band:#2c4d80;
  --ink:#1d1d1d;
  --text:#555;
  --muted:#777;
  --line:#d8d8d8;
  --grey-bg:#f3f3f3;
  --band-bg:#eeeeee;
  --white:#fff;
}
*{margin:0;padding:0;box-sizing:border-box}
html,body{width:1200px;height:3056px;overflow:hidden}
body{font-family:'Roboto',Arial,sans-serif;color:var(--text);background:var(--white);position:relative}
.wrap{width:1004px;margin:0 auto;position:relative}
section,header,footer{position:relative;width:1200px}

/* header */
.site-header{height:88px;border-top:4px solid var(--navy);background:var(--white)}
.site-header .wrap{display:flex;align-items:center;justify-content:space-between;height:84px}
.brand{font-family:'Roboto',sans-serif;font-weight:700;font-size:40px;letter-spacing:2px;color:var(--navy)}
.main-nav{display:flex;align-items:center;gap:0}
.main-nav a{font-size:14px;color:#333;text-decoration:none;margin-left:42px;text-transform:uppercase}
.main-nav a:first-child{margin-left:0}
.nav-sep{margin:0 12px 0 14px;color:#333;font-size:14px}

/* hero */
.hero{height:428px;background:linear-gradient(180deg,#b8c6d4 0%,#9aa9b5 30%,#7b6a5a 60%,#5a6f3e 100%);display:flex;align-items:center;justify-content:center}
.hero h1{font-family:'Open Sans',sans-serif;font-weight:800;font-size:78px;letter-spacing:6px;color:var(--white);margin-top:-20px}
.hero-arrow{position:absolute;top:275px}
.hero-arrow.prev{left:40px}
.hero-arrow.next{right:40px}

/* intro */
.intro{height:365px;text-align:center;padding-top:60px}
.intro h3{font-size:22px;font-weight:500;color:var(--ink)}
.intro h2{font-size:32px;font-weight:300;color:#777;margin-top:12px}
.rule{width:64px;height:2px;background:var(--navy);margin:22px auto 0}
.intro p{font-size:12.5px;line-height:25px;width:820px;margin:26px auto 0;color:var(--text)}
.btn{display:inline-block;border:1px solid #999;padding:0 28px;height:36px;line-height:34px;font-size:13px;color:#555;text-transform:uppercase;text-decoration:none}
.intro .btn{margin-top:30px}

/* features */
.features{height:222px;background:linear-gradient(120deg,#f1f1f1 0%,#e6e6e6 35%,#f3f3f3 55%,#e8e8e8 80%,#f2f2f2 100%)}
.features .wrap{display:flex;padding-top:46px}
.feature{width:362px;display:flex}
.feature svg{flex:none;margin-right:22px}
.feature h4{font-size:19px;font-weight:400;color:var(--ink);margin-bottom:10px}
.feature p{font-size:12.5px;line-height:23px;width:240px}
.feature a{display:block;font-size:11px;color:var(--navy);margin-top:12px;text-decoration:none}

/* what we do */
.what{height:412px}
.what .shot-back{position:absolute;left:112px;top:60px;width:452px;height:282px;background:#e2e2e2}
.what .shot{position:absolute;left:98px;top:72px;width:466px;height:278px;background:linear-gradient(135deg,#b9bcc0 0%,#8f949a 45%,#3b3f47 75%,#9aa6b4 100%)}
.what .copy{position:absolute;left:625px;top:58px;width:478px}
.what h2{font-size:27px;font-weight:500;color:var(--ink)}
.what p{font-size:12.5px;line-height:23px;margin-top:18px}
.what .btn{margin-top:22px}

/* testimonial */
.testimonial{height:386px;background:linear-gradient(180deg,#2e5083 0%,#27487a 100%);text-align:center;color:var(--white);padding-top:55px}
.testimonial h2{font-size:27px;font-weight:500}
.avatar{width:84px;height:84px;border-radius:50%;border:3px solid #e9eef5;background:linear-gradient(160deg,#d7dde3,#8b96a3);margin:26px auto 0}
.testimonial p{font-size:13px;line-height:26px;width:660px;margin:28px auto 0}
.testimonial .name{font-size:15px;font-weight:500;margin-top:14px}
.testimonial .role{font-size:12px;margin-top:4px;opacity:.85}

/* team */
.team{height:377px;text-align:center;padding-top:60px}
.team h2,.blog h2{font-size:27px;font-weight:500;color:var(--ink)}
.team-grid{position:absolute;top:122px;left:98px;width:1004px}
.member{position:absolute;width:177px;height:184px;background:linear-gradient(180deg,#8e8e8e 0%,#5c5c5c 100%)}
.member .tag{position:absolute;left:18px;bottom:0;width:141px;height:38px;background:var(--white);padding-top:4px}
.member .tag b{display:block;font-size:14px;font-weight:400;color:var(--ink)}
.member .tag span{display:block;font-size:12px;color:var(--navy);margin-top:2px}

/* blog */
.blog{height:465px;background:var(--grey-bg);text-align:center;padding-top:62px}
.post{position:absolute;top:128px;width:312px;text-align:left}
.post .thumb{height:160px}
.post h5{font-size:15px;font-weight:500;color:var(--ink);margin-top:22px}
.post p{font-size:11.5px;line-height:24px;margin-top:8px;color:#666}

/* footer */
.site-footer{height:258px;border-top:3px solid var(--navy);background:var(--white)}
.col{position:absolute;top:40px}
.col h6{font-size:16px;font-weight:500;color:var(--ink);letter-spacing:.5px;margin-bottom:20px}
.col ul{list-style:none}
.col li{font-size:11.5px;color:#555;line-height:30px}
.contact li{display:flex;line-height:20px;margin-bottom:14px}
.contact li svg{flex:none;margin:3px 14px 0 0}
.socials{display:flex;gap:6px}
.socials span{width:26px;height:26px;border:1px solid #999;border-radius:50%}
.bottom-bar{position:absolute;left:0;top:2998px;width:1200px;height:58px;background:#eaeaea;text-align:center;line-height:58px;font-size:12px;color:#444}
</style>
</head>
<body>

<header class="site-header">
  <div class="wrap">
    <div class="brand">KOVA</div>
    <nav class="main-nav">
      <a href="#">Home</a><a href="#">Services</a><a href="#">Team</a><a href="#">Careers</a><a href="#">Blog</a><a href="#">Contact Us</a>
      <span class="nav-sep">|</span>
      <svg width="14" height="14" viewBox="0 0 14 14"><circle cx="5.8" cy="5.8" r="4.3" fill="none" stroke="#22406f" stroke-width="2"/><line x1="9" y1="9" x2="13" y2="13" stroke="#22406f" stroke-width="2.4"/></svg>
    </nav>
  </div>
</header>

<section class="hero" role="img" aria-label="Aerial view of an old Swiss city with church spire, rooftops and green hills">
  <h1>WE ARE KOVA</h1>
  <svg class="hero-arrow prev" width="16" height="54" viewBox="0 0 16 54"><polyline points="14,2 2,27 14,52" fill="none" stroke="#fff" stroke-width="2"/></svg>
  <svg class="hero-arrow next" width="16" height="54" viewBox="0 0 16 54"><polyline points="2,2 14,27 2,52" fill="none" stroke="#fff" stroke-width="2"/></svg>
</section>

<section class="intro">
  <h3>Legal Startup Company</h3>
  <h2>Our Commitment to Excellence Has Been Recognized</h2>
  <div class="rule"></div>
  <p>Contrary to popular belief, Lorem Ipsum is not simply random text. It has roots in a piece of classical Latin literature from 45 BC, making it over 2000 years old. Martin Keller, a Latin professor at Aarberg College in Bern</p>
  <a class="btn" href="#">Read More</a>
</section>

<section class="features">
  <div class="wrap">
    <div class="feature">
      <svg width="40" height="30" viewBox="0 0 40 30"><polyline points="2,2 2,28 38,28" fill="none" stroke="#22406f" stroke-width="3"/><polyline points="8,22 16,13 22,18 33,7" fill="none" stroke="#22406f" stroke-width="3"/><polygon points="28,5 36,4 35,12" fill="#22406f"/></svg>
      <div><h4>Business Plan</h4><p>Lorem ipsum dolor sit amet, consectetur adipiscing elit. Nam viverra to euismod odio, gravida pellentesque</p><a href="#">Read More &gt;&gt;</a></div>
    </div>
    <div class="feature">
      <svg width="38" height="30" viewBox="0 0 38 30"><rect x="13" y="1" width="12" height="7" fill="none" stroke="#22406f" stroke-width="3"/><rect x="1" y="7" width="36" height="22" rx="2" fill="#22406f"/><rect x="16" y="15" width="6" height="5" fill="#fff"/></svg>
      <div><h4>Funding Stragey</h4><p>Lorem ipsum dolor sit amet, consectetur adipiscing elit. Nam viverra to euismod odio, gravida pellentesque</p><a href="#">Read More &gt;&gt;</a></div>
    </div>
    <div class="feature">
      <svg width="38" height="30" viewBox="0 0 38 30"><rect x="1" y="3" width="36" height="24" rx="2" fill="#22406f"/><rect x="5" y="7" width="28" height="16" fill="none" stroke="#fff" stroke-width="1.5"/><circle cx="19" cy="15" r="5" fill="#fff"/></svg>
      <div><h4>Saving Money</h4><p>Lorem ipsum dolor sit amet, consectetur adipiscing elit. Nam viverra to euismod odio, gravida pellentesque</p><a href="#">Read More &gt;&gt;</a></div>
    </div>
  </div>
</section>

<section class="what">
  <div class="shot-back"></div>
  <div class="shot" role="img" aria-label="Team of business professionals standing together in a city street"></div>
  <div class="copy">
    <h2>What We Do</h2>
    <p>Contrary to popular belief, Lorem Ipsum is not simply random text. It has roots in a piece of classical Latin literature from 45 BC, making it over 2000 years old. Martin Keller, a Latin professor at Aarberg College in Bern</p>
    <p>There are many variations of passages of Lorem Ipsum available, but the majority have suffered alteration in some form, by injected humour, or randomised words which don't look even slightly believable. If you are going to use a passage of Lorem Ipsum, you need to be sure there isn't anything embarrassing</p>
    <a class="btn" href="#">Read More</a>
  </div>
</section>

<section class="testimonial">
  <h2>What Our Client Says</h2>
  <div class="avatar" role="img" aria-label="Client portrait"></div>
  <p>I must explain to you how all this mistaken idea of denouncing pleasure and praising pain was born and I will give you a complete account of the system, and expound the actual teachings of the great explorer of the truth</p>
  <div class="name">Lena Morandi</div>
  <div class="role">Installer</div>
</section>

<section class="team">
  <h2>Our Expert Team</h2>
  <div class="team-grid">
    <div class="member" style="left:0" role="img" aria-label="Team member portrait"><div class="tag"><b>Ms. Mira Solberg</b><span>CEO</span></div></div>
    <div class="member" style="left:207px" role="img" aria-label="Team member portrait"><div class="tag"><b>Ms. Mira Solberg</b><span>CEO</span></div></div>
    <div class="member" style="left:414px" role="img" aria-label="Team member portrait"><div class="tag"><b>Ms. Mira Solberg</b><span>CEO</span></div></div>
    <div class="member" style="left:621px" role="img" aria-label="Team member portrait"><div class="tag"><b>Ms. Mira Solberg</b><span>CEO</span></div></div>
    <div class="member" style="left:827px" role="img" aria-label="Team member portrait"><div class="tag"><b>Ms. Mira Solberg</b><span>CEO</span></div></div>
  </div>
</section>

<section class="blog">
  <h2>Our Recent Blog Post</h2>
  <article class="post" style="left:98px">
    <div class="thumb" role="img" aria-label="Desk with charts, tablet and hands reviewing documents" style="background:linear-gradient(135deg,#c9a36f,#e9e4dc 55%,#6f8fb8)"></div>
    <h5>SED PERSPICIATIS UNDE OMNIS</h5>
    <p>Lorem ipsum dolor sit amet, consectetuer. Proin gravida nibh vel velit auctor aliquet. the far Aenean sollicitudi ravida.Lorem ipsum dolor sit amet.</p>
  </article>
  <article class="post" style="left:444px">
    <div class="thumb" role="img" aria-label="Colleagues discussing a document in a bright office" style="background:linear-gradient(135deg,#6c7480,#e8e6e2 50%,#c7cdd6)"></div>
    <h5>SED PERSPICIATIS UNDE OMNIS</h5>
    <p>Lorem ipsum dolor sit amet, consectetuer. Proin gravida nibh vel velit auctor aliquet. the far Aenean sollicitudi ravida.Lorem ipsum dolor sit amet.</p>
  </article>
  <article class="post" style="left:790px">
    <div class="thumb" role="img" aria-label="Two women in conversation at a meeting" style="background:linear-gradient(135deg,#dfe3e8,#4f6f9a 45%,#d7a53a 75%,#3fa79a)"></div>
    <h5>SED PERSPICIATIS UNDE OMNIS</h5>
    <p>Lorem ipsum dolor sit amet, consectetuer. Proin gravida nibh vel velit auctor aliquet. the far Aenean sollicitudi ravida.Lorem ipsum dolor sit amet.</p>
  </article>
</section>

<footer class="site-footer">
  <div class="col contact" style="left:98px;width:220px">
    <h6>CONTACT US</h6>
    <ul>
      <li><svg width="10" height="13" viewBox="0 0 10 13"><path d="M5 0a5 5 0 0 0-5 5c0 4 5 8 5 8s5-4 5-8a5 5 0 0 0-5-5z" fill="#22406f"/><circle cx="5" cy="5" r="1.8" fill="#fff"/></svg>2000 years old. Martin Keller, a Latin professor at</li>
      <li><svg width="12" height="12" viewBox="0 0 12 12"><path d="M2 0h3l1 3-2 1.5a7 7 0 0 0 3.5 3.5L9 6l3 1v3a2 2 0 0 1-2 2A10 10 0 0 1 0 2a2 2 0 0 1 2-2z" fill="#22406f"/></svg>Phone - 123 321 4563</li>
      <li><svg width="12" height="12" viewBox="0 0 12 12"><rect x="0" y="4" width="12" height="8" rx="1" fill="#22406f"/><rect x="3" y="0" width="6" height="5" fill="#22406f"/></svg>Fax - 789 654 1230</li>
      <li><svg width="12" height="10" viewBox="0 0 12 10"><rect x=".7" y=".7" width="10.6" height="8.6" fill="none" stroke="#22406f" stroke-width="1.4"/><polyline points="1,1 6,5.5 11,1" fill="none" stroke="#22406f" stroke-width="1.4"/></svg>E-mail - example@company .com</li>
    </ul>
  </div>
  <div class="col" style="left:367px">
    <h6>QUICK LINKS</h6>
    <ul><li>About us</li><li>Services</li><li>What we do</li><li>Blog</li></ul>
  </div>
  <div class="col" style="left:536px">
    <h6>OUR POLICY</h6>
    <ul><li>Help &amp; Contact</li><li>Register entry</li><li>Business identification</li><li>Affiliates</li></ul>
  </div>
  <div class="col" style="left:722px">
    <h6>COMMUNITY</h6>
    <ul><li>Guidlines</li><li>Terms &amp; conditions</li><li>privacy policy</li><li>site map</li><li>Contact us</li></ul>
  </div>
  <div class="col" style="left:910px">
    <h6>SOCIAL MEDIA</h6>
    <div class="socials"><span></span><span></span><span></span><span></span><span></span><span></span></div>
  </div>
</footer>

<div class="bottom-bar">Copyrights@2017Compny name , All rights Reserved</div>

</body>
</html>
```